Business Card Design for Varomir Facility Services

We are looking for a Business Card Design for the Company "Varomir Facility Services."
Front side:
- Company Logo (small)
- Company Name, address, pohone, website and personal data.
- white background, for text e.g. company colors (blue or green like in the logo)
Please use following data:
Company data:
Varomir Facility Services Kostelac
Birkenhaldweg 14
6418 Felsbach
www.varomir-fs.ch
Person data:
Tarik Kostelac
Geschäftsführer
+41 76 519 47 83
info@varomir-fs.ch
Back side:
could be colored in blue or green
please use a big logo sing and some smaller icons to say what is all beeing offered in facility services, like cleaning, maintenance cleaning
industrial cleaning, caretaking, gardening, disposal. There is no need for everyone of the icons if there are similar or an icon is standing for more of them.
colors to use:
blue: HEX 246BB0
green: HEX 52B33E

```html
<!DOCTYPE html>
<html lang="de">
<head>
<meta charset="utf-8">
<title>Varomir Facility Services – Business Card</title>
<link href="https://fonts.googleapis.com/css2?family=Roboto:wght@400;500;700;900&display=swap" rel="stylesheet">
<style>
  :root {
    --blue: #246BB0;
    --green: #52B33E;
    --white: #ffffff;
    --ink: #1b1b1b;
    --stage: #d9d9d9;
  }
  * { box-sizing: border-box; margin: 0; padding: 0; }
  html, body {
    width: 1200px; height: 1200px; overflow: hidden;
    background: var(--stage);
    font-family: "Roboto", Arial, sans-serif;
  }
  .stage {
    width: 1200px; height: 1200px;
    display: flex; flex-direction: column; align-items: center; justify-content: center;
    gap: 44px;
  }
  .card {
    position: relative;
    width: 840px; height: 520px;
    border-radius: 34px;
    overflow: hidden;
  }

  /* ---------- back side ---------- */
  .card-back {
    background: var(--blue);
    color: var(--white);
    display: flex; flex-direction: column; align-items: center;
    padding-top: 78px;
  }
  .brand {
    display: flex; align-items: center; gap: 22px;
    font-weight: 700;
  }
  .brand-dot { flex: none; border-radius: 50%; }
  .card-back .brand-dot { width: 86px; height: 86px; background: var(--white); }
  .brand-name { display: flex; flex-direction: column; line-height: 1; }
  .brand-name .main { letter-spacing: 0.08em; }
  .card-back .brand-name .main { font-size: 82px; }
  .card-back .brand-name .sub { font-size: 34px; letter-spacing: 0.2em; margin-top: 10px; }

  .services {
    list-style: none;
    display: flex; gap: 50px; margin-top: 70px;
  }
  .service {
    display: flex; flex-direction: column; align-items: center; width: 128px;
    text-align: center;
  }
  .service-badge {
    width: 104px; height: 104px; border-radius: 50%;
    border: 3px solid var(--white);
    padding: 7px;
  }
  .service-badge .icon-area {
    width: 100%; height: 100%; border-radius: 50%;
    background: var(--white);
  }
  .service-label {
    margin-top: 12px;
    font-size: 15px; font-weight: 700; letter-spacing: 0.02em;
    line-height: 1.1; text-transform: uppercase;
  }

  /* ---------- front side ---------- */
  .card-front { background: var(--white); }
  .card-front .brand {
    position: absolute; left: 70px; top: 58px;
    color: var(--blue);
  }
  .card-front .brand-dot { width: 92px; height: 92px; background: var(--green); }
  .card-front .brand-name .main { font-size: 86px; }
  .card-front .brand-name .sub { font-size: 36px; letter-spacing: 0.2em; margin-top: 10px; }

  .person {
    position: absolute; left: 0; right: 0; top: 238px;
    text-align: center;
  }
  .person-name {
    color: var(--blue); font-size: 30px; font-weight: 900; letter-spacing: 0.01em;
  }
  .person-role { color: var(--ink); font-size: 19px; margin-top: 2px; }

  .contact-band {
    position: absolute; left: 0; right: 0; top: 318px; height: 168px;
    background: var(--blue);
    color: var(--white);
    display: flex; align-items: center; justify-content: center;
  }
  .contact-band::before,
  .contact-band::after {
    content: ""; position: absolute; left: 0; right: 0; height: 4px; background: var(--green);
  }
  .contact-band::before { top: -10px; }
  .contact-band::after { bottom: -10px; }

  .company-address {
    font-style: normal;
    text-align: right; font-size: 20px; line-height: 1.3; padding-right: 28px;
  }
  .company-address .company { font-weight: 700; }
  .divider { width: 2px; height: 112px; background: var(--white); }
  .contact-list { list-style: none; padding-left: 28px; font-size: 21px; line-height: 1.35; }
  .contact-list li { display: flex; align-items: center; gap: 12px; }
  .contact-list svg { width: 20px; height: 20px; flex: none; }
  .contact-list b { font-weight: 700; }
</style>
</head>
<body>
<main class="stage">

  <section class="card card-back" aria-label="Back side">
    <div class="brand">
      <span class="brand-dot"></span>
      <div class="brand-name">
        <span class="main">VAROMIR</span>
        <span class="sub">FACILITY SERVICES</span>
      </div>
    </div>
    <ul class="services">
      <li class="service">
        <div class="service-badge"><div class="icon-area" role="img" aria-label="Icon: bucket and brush for maintenance cleaning"></div></div>
        <span class="service-label">Maintenance<br>Cleaning</span>
      </li>
      <li class="service">
        <div class="service-badge"><div class="icon-area" role="img" aria-label="Icon: handshake in a heart for caretaking"></div></div>
        <span class="service-label">Caretaking</span>
      </li>
      <li class="service">
        <div class="service-badge"><div class="icon-area" role="img" aria-label="Icon: flower in a pot for gardening"></div></div>
        <span class="service-label">Gardening</span>
      </li>
      <li class="service">
        <div class="service-badge"><div class="icon-area" role="img" aria-label="Icon: waste bin for disposal"></div></div>
        <span class="service-label">Disposal</span>
      </li>
    </ul>
  </section>

  <section class="card card-front" aria-label="Front side">
    <div class="brand">
      <span class="brand-dot"></span>
      <div class="brand-name">
        <span class="main">VAROMIR</span>
        <span class="sub">FACILITY SERVICES</span>
      </div>
    </div>

    <div class="person">
      <p class="person-name">TARIK KOSTELAC</p>
      <p class="person-role">Geschäftsführer</p>
    </div>

    <div class="contact-band">
      <address class="company-address">
        <span class="company">Varomir Facility Services Kostelac</span><br>
        Birkenhaldweg 14<br>
        6418 Felsbach
      </address>
      <span class="divider"></span>
      <ul class="contact-list">
        <li>
          <svg viewBox="0 0 24 24" fill="#fff" aria-hidden="true"><path d="M6.6 10.8a15.1 15.1 0 0 0 6.6 6.6l2.2-2.2c.3-.3.7-.4 1-.2 1.1.4 2.3.6 3.6.6.6 0 1 .4 1 1V20c0 .6-.4 1-1 1A17 17 0 0 1 3 4c0-.6.4-1 1-1h3.5c.6 0 1 .4 1 1 0 1.3.2 2.5.6 3.6.1.3 0 .7-.2 1l-2.3 2.2z"/></svg>
          +41 76 519 47 83
        </li>
        <li>
          <svg viewBox="0 0 24 24" fill="none" stroke="#fff" stroke-width="2" aria-hidden="true"><rect x="3" y="5" width="18" height="14" rx="1"/><path d="M3 6l9 7 9-7"/></svg>
          info@varomir-fs.ch
        </li>
        <li>
          <svg viewBox="0 0 24 24" fill="none" stroke="#fff" stroke-width="1.8" aria-hidden="true"><circle cx="12" cy="12" r="9"/><path d="M3 12h18M12 3c3 3 3 15 0 18M12 3c-3 3-3 15 0 18"/></svg>
          <span>www.<b>varomir-fs</b>.ch</span>
        </li>
      </ul>
    </div>
  </section>

</main>
</body>
</html>
```